Business Card for Vorla Parts Wholesale supplier

Hi There! I need a new business card for our company. We are specialized in selling Vorla parts, mostly we sell new LCD screens for Zelnar and Drelks. I would like to see that back in the design.

You can find the colors and logo's on our website: www.hartuvo.nl

Industry/Entity Type

Business

Contact Information for Business Card

My Details:
Tobias Lindqvist

Phone: 0031687203316
E-mail: Tobias@hartuvo.nl

Slogan: "Because Quality Matters"

Font styles to use
Sans Serif

Colors

Designer to choose colors to be used in the design.

Requirements
Must have
• A Black backside with the Hartuvo logo on it. The front side should be clean with only my contact details.
• But I'm also open for something really different or awesome!
Nice to have
• Remember that we are in the parts & repairing industry, So i'll be handing those business cards mainly to repair companies. Maybe you can do something with that thought :)

```html
<!DOCTYPE html>
<html lang="en">
<head>
<meta charset="utf-8">
<title>Hartuvo Business Card</title>
<link href="https://fonts.googleapis.com/css2?family=Roboto:wght@300;400;700&display=swap" rel="stylesheet">
<style>
  :root {
    --backdrop: #2b2b2d;
    --paper: #ffffff;
    --ink: #1d1d1f;
    --band: #262628;
    --accent: #f07a2a;
    --muted: #707070;
    --back-top: #1a1a1a;
    --back-bottom: #050505;
  }
  * { margin: 0; padding: 0; box-sizing: border-box; }
  html, body { width: 1200px; height: 950px; overflow: hidden; }
  body {
    background: var(--backdrop);
    font-family: "Roboto", Arial, sans-serif;
    position: relative;
  }
  .card {
    position: absolute;
    left: 250px;
    width: 700px;
    height: 400px;
    overflow: hidden;
    box-shadow: 0 14px 40px rgba(0,0,0,0.45);
  }
  .card--front { top: 50px; background: var(--paper); }
  .card--back {
    top: 500px;
    background: linear-gradient(160deg, var(--back-top) 0%, var(--back-bottom) 70%);
    display: flex; align-items: center; justify-content: center;
  }

  .brand { display: flex; align-items: center; gap: 14px; }
  .brand__dot { width: 40px; height: 40px; border-radius: 50%; background: var(--accent); }
  .brand__name { font-weight: 700; font-size: 54px; letter-spacing: 1px; line-height: 1; }
  .card--front .brand { position: absolute; top: 48px; right: 44px; }
  .card--front .brand__name { color: var(--ink); }
  .card--back .brand__dot { width: 64px; height: 64px; }
  .card--back .brand__name { color: var(--paper); font-size: 88px; }

  .contact {
    position: absolute; top: 150px; left: 44px;
    font-size: 15px; font-weight: 300; color: var(--muted); line-height: 1.6;
  }
  .contact__label { color: var(--accent); font-weight: 400; }
  .contact__web { letter-spacing: 4px; }

  .name-band { position: absolute; top: 232px; left: 0; width: 520px; height: 56px; }
  .name-band svg { position: absolute; inset: 0; }
  .name-band__text {
    position: absolute; left: 44px; top: 50%; transform: translateY(-50%);
    color: var(--accent); font-weight: 700; font-size: 24px;
  }

  .slogan {
    position: absolute; top: 312px; left: 250px;
    color: var(--accent); font-size: 17px; line-height: 1.35; font-weight: 400;
  }
</style>
</head>
<body>
  <section class="card card--front" aria-label="Business card front">
    <div class="brand">
      <span class="brand__dot"></span>
      <span class="brand__name">hartuvo</span>
    </div>

    <div class="contact">
      <p><span class="contact__label">P :</span> 0031687203316</p>
      <p><span class="contact__label">E :</span> Tobias@hartuvo.nl</p>
      <p class="contact__web">www.hartuvo.nl</p>
    </div>

    <div class="name-band">
      <svg viewBox="0 0 520 56" width="520" height="56" preserveAspectRatio="none" aria-hidden="true">
        <polygon points="0,0 520,0 480,56 0,56" fill="var(--band)"/>
      </svg>
      <span class="name-band__text">Tobias Lindqvist</span>
    </div>

    <p class="slogan">Because<br>Quality Matters</p>
  </section>

  <section class="card card--back" aria-label="Business card back">
    <div class="brand">
      <span class="brand__dot"></span>
      <span class="brand__name">hartuvo</span>
    </div>
  </section>
</body>
</html>
```